Business card for medical clinic

I need an upmarket, modern medical/health business card for my clinic

Contact Information for Business Card

name, address, email, qr code

```html
<!DOCTYPE html>
<html lang="en">
<head>
<meta charset="utf-8">
<title>Meridian Care Clinic – Business Card</title>
<link href="https://fonts.googleapis.com/css2?family=Cinzel:wght@500&family=Montserrat:wght@400;700&display=swap" rel="stylesheet">
<style>
  :root {
    --backdrop: #2b2b2d;
    --card-white: #ffffff;
    --card-black: #141416;
    --brand-blue: #1b7fc0;
    --brand-navy: #1d3357;
    --accent-sky: #29aee6;
    --text-light: #f2f4f6;
  }
  * { box-sizing: border-box; margin: 0; padding: 0; }
  html, body {
    width: 1200px; height: 880px; overflow: hidden;
    background: var(--backdrop);
  }
  .canvas { position: relative; width: 1200px; height: 880px; }

  .card {
    position: absolute;
    width: 700px; height: 400px;
    border-radius: 28px;
    overflow: hidden;
    box-shadow: 0 10px 30px rgba(0,0,0,.45);
  }

  /* Front */
  .card--front { left: 140px; top: 24px; background: var(--card-white); }
  .brand {
    position: absolute; inset: 0;
    display: flex; align-items: center; justify-content: center; gap: 22px;
  }
  .brand__dot {
    width: 26px; height: 26px; border-radius: 50%;
    background: var(--brand-blue);
  }
  .brand__name {
    font-family: "Cinzel", serif; font-weight: 500;
    color: var(--brand-blue); text-align: center; line-height: 1.15;
  }
  .brand__name .line-main { display: block; font-size: 50px; letter-spacing: 1px; }
  .brand__name .line-sub { display: block; font-size: 22px; letter-spacing: 12px; }

  /* Back */
  .card--back { left: 360px; top: 456px; background: var(--card-black); }
  .back__disc {
    position: absolute; left: 330px; top: -150px;
    width: 460px; height: 460px; border-radius: 50%;
    background: var(--card-white);
  }
  .back__brand {
    position: absolute; left: 44px; top: 38px;
    display: flex; align-items: center; gap: 12px;
  }
  .back__brand .brand__dot { width: 14px; height: 14px; }
  .back__brand .brand__name .line-main { font-size: 22px; }
  .back__brand .brand__name .line-sub { font-size: 11px; letter-spacing: 6px; }

  .contact {
    position: absolute; left: 44px; top: 138px;
    font-family: "Montserrat", sans-serif; color: var(--text-light);
  }
  .contact__head { position: relative; padding-left: 22px; }
  .contact__bar {
    position: absolute; left: 0; top: 6px; width: 9px; height: 52px;
    background: linear-gradient(var(--brand-navy), var(--accent-sky));
  }
  .contact__name {
    font-weight: 700; font-size: 30px; letter-spacing: .5px;
    color: var(--brand-blue); line-height: 1.1;
  }
  .contact__role { font-size: 17px; margin-top: 2px; }
  .contact__address { font-size: 17px; line-height: 1.35; margin: 24px 0 0 22px; }
  .contact__list { list-style: none; margin: 20px 0 0 0; font-size: 17px; line-height: 1.6; }
  .contact__list li { display: flex; align-items: center; gap: 10px; }
  .contact__list svg { width: 14px; height: 14px; fill: var(--accent-sky); flex: none; }
</style>
</head>
<body>
<main class="canvas">

  <section class="card card--front" aria-label="Card front">
    <div class="brand">
      <span class="brand__dot"></span>
      <h1 class="brand__name">
        <span class="line-main">MERIDIAN CARE</span>
        <span class="line-sub">CLINIC</span>
      </h1>
    </div>
  </section>

  <section class="card card--back" aria-label="Card back">
    <div class="back__disc"></div>

    <div class="back__brand">
      <span class="brand__dot"></span>
      <p class="brand__name">
        <span class="line-main">MERIDIAN CARE</span>
        <span class="line-sub">CLINIC</span>
      </p>
    </div>

    <div class="contact">
      <div class="contact__head">
        <span class="contact__bar"></span>
        <h2 class="contact__name">DANIEL HART</h2>
        <p class="contact__role">Managing Director</p>
      </div>
      <p class="contact__address">Your address, City<br>State, Zip 1234</p>
      <ul class="contact__list">
        <li>
          <svg viewBox="0 0 24 24" aria-hidden="true"><path d="M6.6 10.8a15.1 15.1 0 0 0 6.6 6.6l2.2-2.2a1 1 0 0 1 1-.25 11.4 11.4 0 0 0 3.6.57 1 1 0 0 1 1 1V20a1 1 0 0 1-1 1A17 17 0 0 1 3 4a1 1 0 0 1 1-1h3.5a1 1 0 0 1 1 1c0 1.25.2 2.45.57 3.6a1 1 0 0 1-.25 1z"/></svg>
          123 456 789
        </li>
        <li>
          <svg viewBox="0 0 24 24" aria-hidden="true"><path d="M2 5h20v14H2zm2 2v.4l8 5 8-5V7zm0 2.8V17h16V9.8l-8 5z"/></svg>
          info@youremail.com
        </li>
        <li>
          <svg viewBox="0 0 24 24" aria-hidden="true"><circle cx="12" cy="12" r="10"/></svg>
          www.yourwebsite.com
        </li>
      </ul>
    </div>
  </section>

</main>
</body>
</html>
```